Broschüre für Sicherheitsdienstleistungen
Zielgruppe
Sicherheitsunternehmen
Hallo,
Wir möchten gerne eine Broschüre (ca. 12 Seiten) gestalten lassen wo alle unsere verschiedene Dienstleistungen Beschrieben werden und unser unternehmen vorgestellt wird an den Kunden.
Als Hard copy Version von unsere neue Seite : http://kwr.baustellenmappe-beispiel.de
Das Design soll Freundlich und Modern Gestaltet werden.
Farbtöne gerne in Weiss und Dunkel Blau
Produktdetails :
Rückendrahtheftung links, 4/4-farbig (beidseitiger Druck, CMYK)
ab 250 g wird der Umschlag zusätzlich genutet
Veredelung Umschlag
beidseitiger UV-Lack glänzend
Veredelung Innenteil
Format
DIN A4 (21 x 29,7 cm)
Details: Hochformat
Seitenanzahl ca. 10 - 12 (Excl. Umschlag)
Material Umschlag
250g Bilderdruck glänzend
Material Innenteil
New Website Design :
http://kwr.baustellenmappe-beispiel.de

```html
<!DOCTYPE html>
<html lang="de">
<head>
<meta charset="utf-8">
<title>Broschüre – Veranstaltungsschutz & Baustellenüberwachung</title>
<link href="https://fonts.googleapis.com/css2?family=Fira+Sans:wght@400;500&family=Fira+Sans+Condensed:wght@500;600&family=Arimo:wght@700&display=swap" rel="stylesheet">
<style>
:root{
  --navy:#3b5270;
  --navy-deep:#1c2a44;
  --panel:rgba(62,86,118,0.93);
  --slate:#4c6788;
  --ink:#1d1d1d;
  --paper:#ffffff;
  --white:#ffffff;
}
*{margin:0;padding:0;box-sizing:border-box}
html,body{width:1200px;height:848px;overflow:hidden;background:var(--paper)}
.spread{position:relative;width:1200px;height:848px;font-family:"Fira Sans",sans-serif;color:var(--ink)}
.page{position:absolute;top:0;height:848px;width:600px;overflow:hidden}
.page--left{left:0;background:var(--paper)}
.page--right{left:600px;background:var(--navy-deep)}

.hero-photo{position:absolute;left:0;top:0;width:600px;height:290px;
  background:radial-gradient(circle at 30% 40%,#e25ab0 0,transparent 45%),
             radial-gradient(circle at 70% 60%,#c04fc7 0,transparent 45%),
             radial-gradient(circle at 50% 20%,#f0d24a 0,transparent 35%),
             linear-gradient(135deg,#b63b9a,#6a3b9e 55%,#d8b23a)}
.site-photo{position:absolute;inset:0;
  background:linear-gradient(180deg,#1a2744 0%,#2b4a78 35%,#5a7ba0 62%,#c98a5a 85%,#2a2a30 100%)}

.page-no{position:absolute;top:0;width:30px;height:36px;background:var(--navy);color:var(--white);
  font:600 17px/36px "Fira Sans Condensed",sans-serif;text-align:center}
.page--left .page-no{left:37px}
.page--right .page-no{left:533px;background:#3d5677}

.brand-tag{position:absolute;height:19px;padding:0 10px;font:600 14px/19px "Fira Sans Condensed",sans-serif;letter-spacing:.3px}
.page--left .brand-tag{left:37px;top:271px;background:var(--navy);color:var(--white)}
.page--right .brand-tag{left:62px;top:71px;background:var(--white);color:var(--navy)}

.title{position:absolute;font:600 30px/1 "Fira Sans Condensed",sans-serif;letter-spacing:.4px;
  padding-bottom:3px;border-bottom:1.5px solid currentColor}
.page--left .title{left:36px;top:306px;color:var(--navy)}
.page--right .title{left:63px;top:107px;color:var(--white);font-size:29px}

.intro{position:absolute;font-size:10.6px;line-height:16.2px;text-align:justify;letter-spacing:.15px}
.page--left .intro{left:36px;top:358px;width:528px;color:var(--slate)}
.page--right .intro{left:63px;top:173px;width:477px;color:var(--white)}

.columns{position:absolute;left:36px;top:440px;width:528px;display:flex;gap:17px}
.col{width:164px;font-size:8.3px;line-height:10.9px;text-align:justify;hyphens:auto}
.col p{margin-bottom:0}
.col .sub{margin-top:11px}
.hl{display:inline;background:var(--navy);color:var(--white);font:700 8.4px/10.9px Arimo,sans-serif;
  box-decoration-break:clone;-webkit-box-decoration-break:clone;padding:0 1px}
.col h3{font-weight:700;margin-bottom:11px;text-align:justify}
.col h3+p{margin-top:0}
.col .gap{margin-top:11px}

.panel{position:absolute;left:36px;top:36px;width:527px;height:760px;background:var(--panel)}
.section{position:absolute;left:63px;width:477px;color:var(--white)}
.section h3{display:inline-block;background:var(--white);color:var(--navy);
  font:500 8.6px/12px "Fira Sans Condensed",sans-serif;padding:0 2px;margin-bottom:9px}
.section p{font-size:8.1px;line-height:10.9px;text-align:justify;hyphens:auto}
</style>
</head>
<body>
<div class="spread">

  <section class="page page--left">
    <div class="hero-photo" role="img" aria-label="Foto: fröhliche Festivalgäste mit bunten Sonnenbrillen, bedeckt mit Farbpulver"></div>
    <div class="page-no">10</div>
    <div class="brand-tag">WALDMARK SECUR</div>
    <h1 class="title">VERANSTALTUNGSSCHUTZ</h1>
    <p class="intro">Sie wünschen sich umfassende Sicherheit für Ihre Veranstaltung? Dann hat die Waldmark Secur den passenden Service für Sie. Im Bereich Veranstaltungsschutz wissen wir genau, worauf es beim Thema Sicherheit für Events ankommt. Wir schützen jede Art von Veranstaltung zuverlässig und tragen so zu ihrem Gelingen bei.</p>

    <div class="columns">
      <div class="col">
        <h3><span class="hl">Schutz für Veranstaltungen aller Art</span></h3>
        <p>Die Waldmark Secur GmbH hat bereits zahlreiche Veranstaltungen erfolgreich abgesichert. Ob Sie ein Festival, Konzert oder Filmpremieren durchführen: Auf Ihren Sicherheitsprofi können Sie sich in Sachen Veranstaltungsschutz vollends verlassen. Wir kümmern uns darum, dass Ihr Event wie geplant und ohne Zwischenfälle abläuft. Unerwünschte Personen kommen genauso wenig auf das Veranstaltungsgelände wie Vandalen eine Chance zum Randalieren haben. Unsere Mitarbeiter haben alles im Griff, erkennen gefährliche Situationen bereits im Vorfeld und behalten auch im Ernstfall einen kühlen Kopf.</p>
        <h3 class="sub"><span class="hl">Ihr Profi für Eventschutz</span></h3>
        <p>Bei der Waldmark Secur arbeiten erfahrene Sicherheitsprofis. Unser Team ist umfassend in allen relevanten Sicherheitsaspekten geschult und kennt sich mit dem Thema Veranstaltungsschutz bestens aus. Durch regelmäßige Auffrischungskurse und Sonderseminare stellen wir außerdem sicher, dass unser Personal stets mit zeitgemäßem Know-how ans Werk geht. So können Sie sich zu jeder Zeit auf Profi-Service und umfassende Sicherheit verlassen.</p>
      </div>
      <div class="col">
        <h3><span class="hl">Veranstaltungsschutz: Perfekt organisiert und effizient</span></h3>
        <p>Den Veranstaltungsschutz für Ihr Event koordiniert vor Ort einer unserer erfahrenen Einsatzleiter. Durch ihn werden alle beteiligten Mitarbeiter der Waldmark Secur genauestens über den Veranstaltungsablauf instruiert. Mit einem umfassenden Briefing werden sie in ihre Position eingewiesen, über ihre Aufgaben unterrichtet und erhalten alle Infos zu besonderen Kundenwünschen. Auch während der Veranstaltung steht der Einsatzleiter in ständiger Kommunikation mit seinem Team. Wir garantieren:<br>Der Veranstaltungsschutz durch die Waldmark Secur ist perfekt organisiert und absolut effizient.</p>
        <h3 class="sub"><span class="hl">Individuelles Konzept mit genauer Planung</span></h3>
        <p>Bei uns bekommen Sie keine x-beliebige Sicherheitslösung. Denn im Unterschied zu vielen anderen Unternehmen gehen wir genau auf Ihre individuellen Bedürfnisse ein.<br>So machen wir uns ein umfassendes Bild vom Ablauf und den Örtlichkeiten Ihrer Veranstaltung. Außerdem beziehen wir stets alle am Event mitwirkenden Parteien in die Planung ein. Wir</p>
      </div>
      <div class="col">
        <p>klären, was wann und wo passiert, ermitteln potenzielle Risiken und positionieren unsere Mitarbeiter an allen sicherheitsrelevanten Punkten. Als Veranstalter können Sie sich vollends auf unsere Praxiserfahrung verlassen. Im Vergleich zu unspezifischen Sicherheitslösungen berücksichtigt unser Veranstaltungsschutz alle Sicherheitsaspekte mit größter Sorgfalt. Den Erfolg Ihrer Veranstaltung können wir dadurch garantieren – zumindest in puncto Sicherheit.</p>
        <p class="gap"><span class="hl">Übrigens</span>: Profitieren Sie auch von unseren Zusatzservices für Veranstaltungen. Neben Sicherheitsteams können Sie bei uns auch Ordner, Verkehrsposten und Hostessen buchen.</p>
        <h3 class="sub" style="margin-top:22px"><span class="hl">Vereinbaren Sie jetzt Ihren Beratungstermin!</span></h3>
        <p>Die Waldmark Secur GmbH bietet Ihnen zuverlässig Sicherheit. Überzeugen Sie sich selbst von unseren umfassenden Leistungen im Bereich Veranstaltungsschutz. Rufen Sie uns kostenlos unter der Nummer 0800 555 0142 an oder nutzen Sie einfach das Kontaktformular. Gerne geben wir Ihnen einen umfassenden Überblick während des Erstberatungsgesprächs. Ihr Sicherheitspartner Waldmark Secur ist für Sie da!</p>
      </div>
    </div>
  </section>

  <section class="page page--right">
    <div class="site-photo" role="img" aria-label="Foto: Baustelle mit Kränen als Silhouette vor Abendhimmel"></div>
    <div class="panel"></div>
    <div class="page-no">11</div>
    <div class="brand-tag">WALDMARK SECUR</div>
    <h2 class="title">BAUSTELLENÜBERWACHUNG</h2>
    <p class="intro">Sie möchten Ihre Baustelle gegen Vandalen und Diebe absichern und wünschen, dass vor Ort alles rechtmäßig und organisiert zugeht? Dann vertrauen Sie auf die Waldmark Secur, denn wir sorgen für umfassende Sicherheit auf Baustellen. Von uns erhalten Sie Baustellenüberwachung auf höchstem Niveau. Wir entwickeln ganzheitliche Konzepte, sichern Ihre Baustelle nachhaltig ab und verhindern Diebstähle, Sachbeschädigungen und andere unerwünschte Zwischenfälle.</p>

    <div class="section" style="top:283px">
      <h3>Sicherheit auf Baustellen</h3>
      <p>Auf die Baustellenüberwachung der Waldmark Secur GmbH können Sie sich zu jeder Zeit verlassen. Je nach Ihren spezifischen Anforderungen und Wünschen übernehmen wir die Einlasskontrollen an Ihrer Baustelle sowie die Tag- und Nachtbewachung. Unsere Mitarbeiter werden bestens von uns geschult und agieren selbst in brenzligen Situationen professionell und fokussiert. Aufgrund unzähliger erfolgreicher Praxiseinsätze weiß unser Team genau, worauf es zu achten gilt. Ganz gleich, ob Sie über ein Kleinprojekt oder eine Großbaustelle verfügen – auf den Baustellenschutz der Waldmark Secur GmbH können Sie zählen.</p>
    </div>
    <div class="section" style="top:381px">
      <h3>Umfassende Baustellenüberwachung und Projektorganisation</h3>
      <p>Waldmark Secur führt am Baustelleneinlass auf Wunsch Personalkontrollen durch. Hierbei überprüfen wir, ob Sicherheitsauflagen eingehalten werden und jeder Arbeiter oder Handwerker über eine rechtmäßige Arbeitsgenehmigung verfügt. Durch unsere Baustellenüberwachung erhalten Sie die Gewissheit, dass am Bau alles korrekt abläuft.<br>Von der Waldmark Secur GmbH bekommen Sie sogar noch mehr: Dank unserer langjährigen Erfahrung im Bereich der Baustellenüberwachung und Projektabwicklung können wir Sie auch bei der Bauleitung, Baulogistik und Baureinigung unterstützen. Sprechen Sie uns an: Gerne erfassen wir Ihren Bedarf und reden gemeinsam über Ihre Möglichkeiten.</p>
    </div>
    <div class="section" style="top:490px">
      <h3>Vertrauen Sie Ihrem Baustellen-Profi</h3>
      <p>Zahlreiche zufriedene Kunden sprechen sich für unsere Dienstleistungen im Bereich der Baustellenüberwachung aus. Waldmark Secur kommt auf Wunsch auch zu Ihnen und sorgt für Sicherheit. Wir machen uns vor Ort ein genaues Bild der Baustelle und erstellen ein umfassendes Sicherheitskonzept. Natürlich können Sie sich darauf verlassen, dass wir alle Schwachpunkte und wichtigen Details in die Planung einbeziehen. Ihr Vorteil: Sie erhalten ein individuelles und genau auf Ihre Bedürfnisse abgestimmtes Schutzkonzept.</p>
    </div>
    <div class="section" style="top:588px">
      <h3>Lassen Sie sich jetzt unverbindlich beraten!</h3>
      <p>Überzeugen Sie sich jetzt selbst von unserem Service. Vereinbaren Sie noch heute Ihren Erstberatungstermin für die Baustellenüberwachung. Wir besprechen potenzielle Maßnahmen und geben Ihnen einen Überblick über die dafür nötigen Einsatzkräfte. Rufen Sie einfach gebührenfrei unter der Telefonnummer 0800 555 0142 an oder nutzen Sie unser Kontaktformular. Ihr Profi für Baustellensicherheit freut sich auf Ihre Anfrage!</p>
    </div>
  </section>

</div>
</body>
</html>
```